Media Services Start-up -- Corporate Website and Logo Design. Inspiration required!

We need a logo design and corporate website design, including coding, for our start-up business.
Vennatra’s value proposition is based on bringing together media content from a vast number of geographies globally, adding human and AI curation, translation and editing, and delivering the content using tailored customer interfaces. On the one hand, the business brings together media coverage from all over the world, and on the other it brings together content, human skills and technology to deliver a supreme customer experience.
Vennatra is a B2B media monitoring and analytics business with emphasis on global customers. Vennatra's service offering is centred around sourcing media content from different markets, processing, storing and delivering the content and insights derived from it using an online platform / mobile app.
The messaging we want to create through the logo is:
- Global scope
- Speed of delivery
- Cost-efficiency
- Multi-lingual
- Tailor-made
- Trustworthy
Target Market(s)
Business to business, PR / Communications, Media, Marketing
Logo Text
Vennatra
Coding
Coded - Design and coding required
Number of Pages Required
5+ page
Font styles to use
Other font styles liked:
- See Design Brief for details
Colors
Designer to choose colors to be used in the design.

```html
<!DOCTYPE html>
<html lang="en">
<head>
<meta charset="utf-8">
<title>Vennatra – Our Solutions</title>
<link href="https://fonts.googleapis.com/css2?family=Roboto:wght@400;500;700&display=swap" rel="stylesheet">
<style>
:root{
  --teal:#3aaf9a;
  --text:#666666;
  --text-dark:#555555;
  --muted:#9a9a9a;
  --line:#eaeaea;
  --white:#ffffff;
  --border:#6b6b6b;
}
*{margin:0;padding:0;box-sizing:border-box}
html,body{width:1200px;height:748px;overflow:hidden;background:var(--white)}
body{font-family:'Roboto',sans-serif;color:var(--text);position:relative}
.site-header{position:absolute;left:0;top:0;width:1200px;height:85px;background:var(--white);box-shadow:0 6px 14px rgba(0,0,0,.06)}
.brand{position:absolute;left:141px;top:16px;font-size:44px;font-weight:700;color:var(--text);letter-spacing:-.5px;line-height:1}
.contact{position:absolute;top:31px;font-size:14px;display:flex;align-items:center;gap:6px;color:var(--text)}
.contact.phone{left:616px}
.contact.mail{left:754px}
.sign-in{position:absolute;left:919px;top:25px;width:96px;height:32px;border:1px solid var(--border);display:flex}
.sign-in .icon{width:31px;border-right:1px solid var(--border);display:flex;align-items:center;justify-content:center}
.sign-in .label{flex:1;display:flex;align-items:center;justify-content:center;font-size:14px}
.menu-btn{position:absolute;left:1026px;top:25px;width:32px;height:32px;border:1px solid var(--border);display:flex;align-items:center;justify-content:center}
.section-title{position:absolute;left:0;width:1200px;top:135px;text-align:center;font-size:32px;font-weight:700;color:var(--text)}
.section-lead{position:absolute;left:340px;width:520px;top:193px;text-align:center;font-size:14px;font-weight:500;line-height:23px;color:var(--text-dark)}
.tab-icon{position:absolute;left:547px;top:266px;width:32px;height:32px;border-radius:50%;background:var(--teal);opacity:.85}
.tabs{position:absolute;left:141px;top:303px;width:918px;height:34px;border-bottom:3px solid var(--line)}
.tab{position:absolute;top:0;font-size:16px;color:var(--muted);white-space:nowrap}
.tab.active{color:var(--text-dark);font-weight:500}
.tab-underline{position:absolute;left:337px;top:31px;width:166px;height:3px;background:var(--teal);box-shadow:0 4px 6px rgba(0,0,0,.15)}
.features{position:absolute;left:141px;top:391px;width:440px;list-style:none}
.features li{position:relative;padding-left:23px;font-size:13px;line-height:19px;margin-bottom:7px}
.features li svg{position:absolute;left:2px;top:5px}
.hero-image{position:absolute;left:636px;top:394px;width:423px;height:259px;background:radial-gradient(circle at 60% 45%,#bfefff 0%,#3bb8ee 35%,#0a7fc4 70%,#04456f 100%);box-shadow:0 10px 24px rgba(0,0,0,.25)}
.nav-arrow{position:absolute;top:496px;width:33px;height:33px;border:1px solid var(--border);display:flex;align-items:center;justify-content:center;background:var(--white)}
.nav-arrow.prev{left:92px;border-color:#aaa}
.nav-arrow.next{left:1075px}
.site-footer{position:absolute;left:0;top:713px;width:1200px;height:35px;background:var(--teal);color:var(--white)}
.copyright{position:absolute;left:141px;top:9px;font-size:13px}
.social{position:absolute;right:141px;top:11px;display:flex;gap:9px}
.social span{width:13px;height:13px;border-radius:50%;background:var(--white)}
</style>
</head>
<body>
<header class="site-header">
  <div class="brand">Vennatra</div>
  <div class="contact phone">
    <svg width="14" height="14" viewBox="0 0 24 24"><path fill="#3aaf9a" d="M6.6 10.8a15.1 15.1 0 0 0 6.6 6.6l2.2-2.2c.3-.3.7-.4 1-.2 1.1.4 2.3.6 3.6.6.6 0 1 .4 1 1V20c0 .6-.4 1-1 1A17 17 0 0 1 3 4c0-.6.4-1 1-1h3.5c.6 0 1 .4 1 1 0 1.3.2 2.5.6 3.6.1.3 0 .7-.2 1z"/></svg>
    +1 555 014 2290
  </div>
  <div class="contact mail">
    <svg width="20" height="14" viewBox="0 0 20 14"><rect x="1" y="1" width="18" height="12" fill="none" stroke="#3aaf9a" stroke-width="1.8"/><path d="M1 1l9 7 9-7M1 13l7-6M19 13l-7-6" fill="none" stroke="#3aaf9a" stroke-width="1.6"/></svg>
    info@vennatra.com
  </div>
  <div class="sign-in">
    <div class="icon"><svg width="15" height="15" viewBox="0 0 16 16"><path d="M2 3h7M2 3v11h11V8" fill="none" stroke="#3aaf9a" stroke-width="1.8"/><path d="M6 10l1-3 6-6 2 2-6 6z" fill="#3aaf9a"/></svg></div>
    <div class="label">Sign In</div>
  </div>
  <div class="menu-btn"><svg width="20" height="16" viewBox="0 0 20 16"><rect y="0" width="20" height="3" fill="#3aaf9a"/><rect y="6.5" width="20" height="3" fill="#3aaf9a"/><rect y="13" width="20" height="3" fill="#3aaf9a"/></svg></div>
</header>

<main>
  <h1 class="section-title">Our Solutions</h1>
  <p class="section-lead">Lorem ipsum dolor sit amet, consectetuer adipiscing elit, sed diam nonummy nibh euismod tincidunt ut laoreet dolore magna aliquam erat volutpat.</p>

  <div class="tab-icon" role="img" aria-label="Content augmentation icon"></div>
  <nav class="tabs">
    <span class="tab" style="left:23px">Content Sourcing</span>
    <span class="tab" style="left:178px">Content Collection</span>
    <span class="tab active" style="left:341px">Content Augmentation</span>
    <span class="tab" style="left:532px">Content Delivery</span>
    <span class="tab" style="left:680px">Media Insights &amp; Consultancy</span>
    <span class="tab-underline"></span>
  </nav>

  <ul class="features">
    <li><svg width="13" height="10" viewBox="0 0 13 10"><path d="M1 5l4 4 7-8" fill="none" stroke="#3aaf9a" stroke-width="1.8"/></svg>We manage and normalise all of the source-level reference data - country, language, reach etc.</li>
    <li><svg width="13" height="10" viewBox="0 0 13 10"><path d="M1 5l4 4 7-8" fill="none" stroke="#3aaf9a" stroke-width="1.8"/></svg>We add editorial validation to ensure only the content required reaches your delivery, removing inevitable noise from source providers</li>
    <li><svg width="13" height="10" viewBox="0 0 13 10"><path d="M1 5l4 4 7-8" fill="none" stroke="#3aaf9a" stroke-width="1.8"/></svg>Tagging - AI and human based tagging to detect locations, people, topics, products, brands, services, etc.</li>
    <li><svg width="13" height="10" viewBox="0 0 13 10"><path d="M1 5l4 4 7-8" fill="none" stroke="#3aaf9a" stroke-width="1.8"/></svg>Human and automated grouping of stories across geographies - clustering, "also-in" groupings etc.</li>
    <li><svg width="13" height="10" viewBox="0 0 13 10"><path d="M1 5l4 4 7-8" fill="none" stroke="#3aaf9a" stroke-width="1.8"/></svg>Translation summarisation - AI Translation or human-created depending on budget, speed of delivery and need.</li>
    <li><svg width="13" height="10" viewBox="0 0 13 10"><path d="M1 5l4 4 7-8" fill="none" stroke="#3aaf9a" stroke-width="1.8"/></svg>Digest authoring - refining the essence of today’s coverage into a concise board-ready output for your organisation</li>
  </ul>

  <div class="hero-image" role="img" aria-label="Glowing blue globe with orbit lines above a desktop computer"></div>

  <div class="nav-arrow prev"><svg width="10" height="18" viewBox="0 0 10 18"><path d="M9 1L1 9l8 8" fill="none" stroke="#999" stroke-width="1.4"/></svg></div>
  <div class="nav-arrow next"><svg width="10" height="18" viewBox="0 0 10 18"><path d="M1 1l8 8-8 8" fill="none" stroke="#555" stroke-width="1.4"/></svg></div>
</main>

<footer class="site-footer">
  <div class="copyright">Copyright © 2019 Vennatra. All Rights Reserved.</div>
  <div class="social"><span></span><span></span><span></span></div>
</footer>
</body>
</html>
```